accomplished personal trainer, former elite gymnast from Russia, highly professional and experienced

Established Fitness trainer in California requires a new web site to attract personal clients and build her group exercise classes.

Here is an example of another fitness trainer's site that I really liked the technology:
http://www.tedvorlam.com

Below I have inserted my current web site: www.quelbornfitnesslodi.com
You can use this web site for the principal content, such as my background and qualifications.

Target Market(s)

Anyone who wants to improve their fitness levels and wellness in general. Anyone who needs directions and instruction on how to exercise. I can train anyone from elite athlete to a disabled person.

Industry/Entity Type

Fitness

Coding

Coded - Design and coding required

Number of Pages Required

5+ page

Font styles to use
Sans Serif

Requirements
Must have
• Easy to navigate main info about me, location, services, contact, benefits of using my services.
• Would be great to create unique representation of me as a trainer and a person, using new technologies and new ideas. Make it different from the other websites. Having its own character. Not too complicated and heavy with information, but an eye catching, useful and fun to navigate.
Nice to have
• new technology, easy access to information, the idea of enjoyment of life, lightness about achieving any goal, spiritual wisdom, unique design. I am planning to insert educational videos, advise, maybe jokes. Sign in, shopping cart, logo, should be easy for me to make changes in content.
Should not have
• cliché, outdated technology, too complicated,

```html
<!DOCTYPE html>
<html lang="en">
<head>
<meta charset="utf-8">
<title>Quelborn Fitness Lodi</title>
<link href="https://fonts.googleapis.com/css2?family=Montserrat:wght@400;500;600;700&family=Open+Sans:wght@400;600&display=swap" rel="stylesheet">
<style>
:root{
  --orange:#f47b0c;
  --orange-deep:#e86a00;
  --ink:#222222;
  --text:#555555;
  --muted:#777777;
  --light:#ececec;
  --band:#e4e4e4;
  --dark:#2b2b2b;
  --btn:#4a4a4a;
  --white:#ffffff;
  --grass:#6f9c42;
  --grass-dark:#557a35;
}
*{margin:0;padding:0;box-sizing:border-box}
html,body{width:1200px;height:2752px;overflow:hidden;background:var(--white)}
body{font-family:"Open Sans",Arial,sans-serif;color:var(--text);position:relative}

/* header */
.site-header{position:absolute;top:0;left:0;width:1200px;height:106px;background:var(--white)}
.brand{position:absolute;left:106px;top:42px;font-family:"Montserrat",sans-serif;font-weight:600;font-size:20px;letter-spacing:1px;color:var(--ink);white-space:nowrap}
.main-nav{position:absolute;left:438px;top:0;height:106px;display:flex}
.main-nav a{position:relative;display:flex;align-items:center;padding:0 34px 0 15px;font-family:"Montserrat",sans-serif;font-size:14.5px;color:#333;text-decoration:none;white-space:nowrap}
.main-nav a:last-child{padding-right:0}
.main-nav a:not(:last-child)::after{content:"";position:absolute;right:0;top:0;width:24px;height:106px;background:
 linear-gradient(to bottom right,transparent 49%,#e6e6e6 50%,transparent 56%) top/100% 50% no-repeat,
 linear-gradient(to top right,transparent 49%,#e6e6e6 50%,transparent 56%) bottom/100% 50% no-repeat}

/* hero */
.hero{position:absolute;top:106px;left:0;width:1200px;height:487px;
 background:linear-gradient(180deg,var(--grass-dark) 0%,#6b9440 40%,#79ab45 75%,#6f9e40 100%)}
.hero-title{position:absolute;top:152px;left:0;width:1200px;text-align:center;color:var(--white);font-family:"Montserrat",sans-serif}
.hero-title .outline{display:block;font-size:66px;font-weight:400;letter-spacing:3px;color:transparent;-webkit-text-stroke:2px var(--white);line-height:74px}
.hero-title .solid{display:block;font-size:62px;font-weight:600;letter-spacing:1px;line-height:70px;text-shadow:0 2px 6px rgba(0,0,0,.25)}
.slider-dots{position:absolute;top:446px;left:550px;display:flex;gap:5px}
.slider-dots span{width:19px;height:19px;border-radius:50%;background:var(--white);border:2px solid rgba(0,0,0,.25)}
.slider-dots span:first-child{background:transparent;border-color:var(--white)}

/* testimonial */
.testimonial{position:absolute;top:593px;left:0;width:1200px;height:238px;background:var(--orange)}
.testimonial p{position:absolute;left:150px;top:50px;width:900px;text-align:center;color:var(--white);font-size:21px;line-height:31px}
.testimonial::after{content:"";position:absolute;left:571px;bottom:-29px;border-left:29px solid transparent;border-right:29px solid transparent;border-top:29px solid var(--orange)}

/* about */
.about{position:absolute;top:831px;left:0;width:1200px;height:463px}
.about-photo{position:absolute;left:106px;top:66px;width:327px;height:340px;border-radius:14px;background:linear-gradient(180deg,#5f8a3a 0%,#76a846 55%,#6a9a3d 100%)}
.about h2{position:absolute;left:481px;top:78px;font-family:"Montserrat",sans-serif;font-weight:500;font-size:34px;color:#333;white-space:nowrap}
.about .copy{position:absolute;left:481px;top:140px;width:640px;font-size:14.5px;line-height:26px;color:var(--text)}
.about .copy p+p{margin-top:26px}
.btn-dark{position:absolute;left:481px;top:343px;width:159px;height:48px;background:var(--btn);border:3px solid #bdbdbd;outline:1px solid var(--btn);display:flex;align-items:center;justify-content:center;color:var(--white);font-family:"Montserrat",sans-serif;font-size:15px}

/* services */
.services{position:absolute;top:1294px;left:0;width:1200px;height:427px;background:var(--light)}
.service{position:absolute;top:30px;width:460px;height:340px}
.service svg{position:absolute;left:0;top:0}
.service h3{position:absolute;left:54px;top:126px;font-family:"Montserrat",sans-serif;font-weight:600;font-size:25px;color:#333;white-space:nowrap}
.service p{position:absolute;left:54px;top:168px;width:445px;font-size:14px;line-height:25px;color:var(--muted)}
.btn-light{position:absolute;left:55px;top:282px;width:153px;height:44px;background:var(--white);border:1px solid #bbb;outline:3px solid var(--white);display:flex;align-items:center;justify-content:center;font-family:"Montserrat",sans-serif;font-size:15px;color:#333}

/* videos */
.videos{position:absolute;top:1721px;left:0;width:1200px;height:395px;background:linear-gradient(180deg,var(--orange) 0%,var(--orange-deep) 60%,#f08a1c 100%)}
.videos h2{position:absolute;top:42px;width:1200px;text-align:center;color:var(--white);font-family:"Montserrat",sans-serif;font-weight:500;font-size:29px}
.video-card{position:absolute;top:101px;width:312px;height:209px;border:5px solid var(--white)}
.video-card .play{position:absolute;left:50%;top:50%;width:56px;height:56px;margin:-28px 0 0 -28px}

/* news */
.news{position:absolute;top:2116px;left:0;width:1200px;height:347px}
.news h2{position:absolute;left:108px;top:64px;font-family:"Montserrat",sans-serif;font-weight:500;font-size:30px;color:var(--orange)}
.news-item{position:absolute;top:128px;width:300px}
.news-item h3{font-family:"Montserrat",sans-serif;font-weight:500;font-size:19px;line-height:26px;color:#222}
.news-item p{margin-top:4px;font-size:14.5px;line-height:25px;color:var(--muted)}
.news-item a{display:block;margin-top:4px;font-size:14px;color:var(--orange);text-decoration:none}

/* newsletter */
.newsletter{position:absolute;top:2463px;left:0;width:1200px;height:143px;background:var(--band)}
.newsletter h2{position:absolute;left:114px;top:56px;font-family:"Montserrat",sans-serif;font-weight:500;font-size:26px;color:#555;white-space:nowrap}
.newsletter h2 span{color:#999}
.field{position:absolute;top:49px;width:239px;height:48px;background:var(--white);padding-left:14px;display:flex;align-items:center;font-size:14px;color:#777}
.btn-subscribe{position:absolute;left:930px;top:49px;width:140px;height:48px;background:var(--dark);border:2px solid #999;outline:1px solid var(--dark);display:flex;align-items:center;justify-content:center;color:var(--white);font-family:"Montserrat",sans-serif;font-size:17px}

/* footer */
.site-footer{position:absolute;top:2606px;left:0;width:1200px;height:146px;background:var(--dark)}
.footer-nav{position:absolute;left:116px;top:44px;display:flex;gap:35px}
.footer-nav a{font-family:"Montserrat",sans-serif;font-size:15px;color:var(--white);text-decoration:none;white-space:nowrap}
.legal{position:absolute;left:116px;top:80px;font-size:12.5px;color:#ccc}
.social{position:absolute;left:933px;top:37px;display:flex;gap:4px}
.social span{width:32px;height:32px;border-radius:50%;border:2px solid var(--white)}
</style>
</head>
<body>

<header class="site-header">
  <div class="brand">QUELBORN FITNESS LODI</div>
  <nav class="main-nav">
    <a href="#">GROUP CLASSES</a>
    <a href="#">PERSONAL TRAINING</a>
    <a href="#">ABOUT QUELBORN</a>
    <a href="#">BLOG</a>
    <a href="#">CONTACT</a>
  </nav>
</header>

<section class="hero" role="img" aria-label="Trainer in a pink top stretching in a split on the grass outdoors">
  <h1 class="hero-title"><span class="outline">WELCOME</span><span class="solid">FITNESS OUTDOORS</span></h1>
  <div class="slider-dots"><span></span><span></span><span></span><span></span></div>
</section>

<section class="testimonial">
  <p>I have known Mila for many years as a fitness trainer and workout class instructor. She is truly one of the very best in the business. Mila is extremely knowledgeable about human physiology and teaching. Her personality is professional, informative, and caring. She would always put “her all” into each of her classes.</p>
</section>

<section class="about">
  <div class="about-photo" role="img" aria-label="Trainer in a pink top kneeling on the lawn"></div>
  <h2>About Quelborn Fitness</h2>
  <div class="copy">
    <p>Mila Orlova is the owner of Quelborn Fitness. She was born and raised in Vologda, Russia where she was a competitive gymnast. Mila graduated from Northgate Academy of Sport with a bachelor degree in Kinesiology and Sports Science. For more than 20 years, Mila has worked as choreographer, gymnastics coach, and fitness professional.</p>
    <p>Mila has a deep knowledge (theory and experience) in many aspects of wellness including spirituality, nutrition, rehabilitation and is working towards a Physical Therapist degree.</p>
  </div>
  <div class="btn-dark">READ MORE</div>
</section>

<section class="services">
  <div class="service" style="left:105px">
    <svg width="190" height="200" viewBox="0 0 190 200" aria-hidden="true">
      <polygon points="90,2 178,52 178,150 90,200 2,150 2,52" fill="none" stroke="#fff" stroke-width="2"/>
      <circle cx="90" cy="76" r="27" fill="none" stroke="#111" stroke-width="4"/>
      <rect x="84" y="40" width="12" height="7" fill="#111"/>
      <path d="M90 76 L90 58 A18 18 0 0 1 105 84 Z" fill="#111"/>
    </svg>
    <h3>Personal Training</h3>
    <p>Private sessions will provide you with the motivation you need to reach your goals. As a nationally certified trainer, Mila will make sure you're working out safely and keep the workouts fresh and exciting so you can achieve your goals.</p>
    <div class="btn-light">READ MORE</div>
  </div>
  <div class="service" style="left:622px">
    <svg width="190" height="200" viewBox="0 0 190 200" aria-hidden="true">
      <polygon points="90,2 178,52 178,150 90,200 2,150 2,52" fill="none" stroke="#fff" stroke-width="2"/>
      <path d="M56 70 L112 60 L118 76 L100 80 A22 22 0 1 1 56 92 Z" fill="none" stroke="#111" stroke-width="4" stroke-linejoin="round"/>
      <circle cx="78" cy="90" r="8" fill="none" stroke="#111" stroke-width="3"/>
    </svg>
    <h3>Group Classes</h3>
    <p>Quelborn Group Exercise classes are designed for people of all fitness levels. Quelborn's group classes take a holistic approach and make sure you work out in a balanced way that feeds your body and spirit.</p>
    <div class="btn-light">READ MORE</div>
  </div>
</section>

<section class="videos">
  <h2>Educational Videos</h2>
  <div class="video-card" style="left:106px;background:linear-gradient(180deg,#6d9546,#7eaa4f)" role="img" aria-label="Video: core exercise on a stability ball in the park">
    <svg class="play" viewBox="0 0 56 56" aria-hidden="true"><circle cx="28" cy="28" r="25" fill="none" stroke="#fff" stroke-width="3"/><polygon points="22,17 40,28 22,39" fill="none" stroke="#fff" stroke-width="3" stroke-linejoin="round"/></svg>
  </div>
  <div class="video-card" style="left:442px;background:linear-gradient(180deg,#7fa24a,#5f8a3c)" role="img" aria-label="Video: group class doing squats outdoors">
    <svg class="play" viewBox="0 0 56 56" aria-hidden="true"><circle cx="28" cy="28" r="25" fill="none" stroke="#fff" stroke-width="3"/><polygon points="22,17 40,28 22,39" fill="none" stroke="#fff" stroke-width="3" stroke-linejoin="round"/></svg>
  </div>
  <div class="video-card" style="left:780px;background:linear-gradient(180deg,#4d6a3a,#5f7f45)" role="img" aria-label="Video: hanging exercise from a tree branch">
    <svg class="play" viewBox="0 0 56 56" aria-hidden="true"><circle cx="28" cy="28" r="25" fill="none" stroke="#fff" stroke-width="3"/><polygon points="22,17 40,28 22,39" fill="none" stroke="#fff" stroke-width="3" stroke-linejoin="round"/></svg>
  </div>
</section>

<section class="news">
  <h2>News &amp; Advices</h2>
  <article class="news-item" style="left:108px">
    <h3>Morbi diam mauris viverra</h3>
    <p>in gravida eu mattis in ante Morbi eget arcu Morbi porta libero id ullamcorper nonummy nibh ligula pulvinar metus eget t placerat molestie Donec dictum lectus non \e</p>
    <a href="#">READ MORE</a>
  </article>
  <article class="news-item" style="left:455px">
    <h3>Donec dictum lectus no</h3>
    <p>in gravida eu mattis in ante Morbi eget arcu Morbi porta libero id ullamcorper nonummy nibh ligula pulvinar metus eget molestie Donec dictum lectus non</p>
    <a href="#">READ MORE</a>
  </article>
  <article class="news-item" style="left:800px">
    <h3>Cum sociis natoque penatibus et magnis dis parturient</h3>
    <p>Morbi porta libero id ullamcorper nonummy nibh ligula pulvinar metus molestie Donec dictum lectus non que habitant</p>
    <a href="#">READ MORE</a>
  </article>
</section>

<section class="newsletter">
  <svg style="position:absolute;left:140px;top:10px" width="240" height="133" viewBox="0 0 240 133" aria-hidden="true">
    <path d="M5 10 H235 V133 H5 Z M5 10 L120 90 L235 10" fill="none" stroke="#d6d6d6" stroke-width="10"/>
  </svg>
  <h2>Newsletter <span>Subscribe</span></h2>
  <div class="field" style="left:433px">Name</div>
  <div class="field" style="left:681px">Email address</div>
  <div class="btn-subscribe">SUBSCRIBE</div>
</section>

<footer class="site-footer">
  <nav class="footer-nav">
    <a href="#">GROUP CLASSES</a>
    <a href="#">PERSONAL TRAINING</a>
    <a href="#">ABOUT QUELBORN</a>
    <a href="#">BLOG</a>
    <a href="#">CONTACT</a>
  </nav>
  <div class="legal">© 2016 Company Name &nbsp;All right reserved &nbsp;Term of Use</div>
  <div class="social" aria-label="Social links"><span></span><span></span><span></span><span></span></div>
</footer>

</body>
</html>
```